Corvane Business Cards

Front of business card will have logo, name, address, & telephone number. Back of card will have a list of services provided - Roads, Substation Pads, Temporary Pads, Site Pads, Land Leveling, Powerline Row Cleaning, Land Clearing, Gates, Fencing, Construction Entrances, Excavation, Trenching, Underground Utilities, Directional Boring, Pile Driving. We are a construction company that uses heavy equipment like bulldozers, motor graders/blades, dump trucks, backhoes, hydro axes, & skid loaders. We build roads, pads, & install electric utility lines & waterlines underground. This logo is new. The word "Construction" can be smaller as uploaded 2 example edited logos. We will be using this card design for many employees.
Target Market(s)
Industrial Electric Powerline, Wind Turbine, Solar Panel, & Water Utility companies.
Contact Information for Business Card
Name/Position - Dwayne Halster - Owner
Address: 4875 FM 309
Harlow Bend, TX 79412
Phone number - (325) 482-5096

```html
<!DOCTYPE html>
<html lang="en">
<head>
<meta charset="utf-8">
<title>Corvane Business Cards</title>
<link href="https://fonts.googleapis.com/css2?family=Poppins:wght@400;600;700&display=swap" rel="stylesheet">
<style>
  :root {
    --maroon: #3b0c18;
    --paper: #f4f4f4;
    --ink: #4a4a4a;
    --grey-band: #9a9a9a;
    --backdrop: #e6e2dd;
    --white: #ffffff;
    --rule: #555555;
  }
  * { margin: 0; padding: 0; box-sizing: border-box; }
  html, body {
    width: 1125px; height: 1200px; overflow: hidden;
    background: var(--backdrop);
    font-family: "Poppins", sans-serif;
  }
  .canvas { position: relative; width: 1125px; height: 1200px; }

  .card {
    position: absolute; left: 150px; width: 825px; height: 470px;
    box-shadow: 0 4px 10px rgba(0,0,0,0.25);
    overflow: hidden;
  }

  /* Front */
  .card-front { top: 98px; background: var(--paper); }
  .brand-front {
    position: absolute; right: 46px; top: 82px;
    color: var(--maroon); text-align: right;
    font-weight: 700; line-height: 1;
  }
  .brand-front .brand-name { display: block; font-size: 66px; letter-spacing: 2px; }
  .brand-front .brand-sub { display: block; font-size: 24px; letter-spacing: 1.5px; margin-top: 12px; }

  .holder { position: absolute; left: 41px; top: 256px; }
  .holder-name { font-size: 27px; font-weight: 700; color: var(--maroon); line-height: 1.15; letter-spacing: 0.3px; }
  .holder-role { font-size: 19px; color: #333; line-height: 1.2; }

  .divider { position: absolute; left: 41px; right: 46px; top: 329px; height: 1px; background: var(--rule); }

  .contact-list { position: absolute; left: 41px; top: 345px; list-style: none; }
  .contact-list li {
    display: flex; align-items: center; gap: 9px;
    font-size: 19.5px; color: var(--ink); line-height: 23px;
  }
  .contact-list svg { width: 15px; height: 15px; flex: none; }

  .address {
    position: absolute; right: 46px; top: 346px;
    text-align: right; font-size: 19.5px; color: var(--ink); line-height: 23px;
    font-style: normal;
  }

  .base-band { position: absolute; left: 0; bottom: 0; width: 100%; height: 11px; }

  /* Back */
  .card-back { top: 631px; background: var(--maroon); }
  .brand-back {
    position: absolute; left: 0; right: 0; top: 150px;
    text-align: center; color: var(--white);
    font-weight: 700; line-height: 1;
  }
  .brand-back .brand-name { display: block; font-size: 96px; letter-spacing: 4px; }
  .brand-back .brand-sub { display: block; font-size: 30px; letter-spacing: 3px; margin-top: 10px; }

  .services {
    position: absolute; left: 0; right: 0; top: 377px;
    text-align: center; color: var(--white);
    font-size: 18.5px; line-height: 22.5px;
  }
  .services p { white-space: nowrap; }
</style>
</head>
<body>
<main class="canvas">

  <section class="card card-front" aria-label="Business card front">
    <div class="brand-front">
      <span class="brand-name">CORVANE</span>
      <span class="brand-sub">CONSTRUCTION</span>
    </div>

    <div class="holder">
      <p class="holder-name">DWAYNE HALSTER</p>
      <p class="holder-role">Owner</p>
    </div>

    <div class="divider"></div>

    <ul class="contact-list">
      <li>
        <svg viewBox="0 0 24 24" aria-hidden="true"><path fill="var(--maroon)" d="M6.6 10.8a15.1 15.1 0 0 0 6.6 6.6l2.2-2.2c.3-.3.7-.4 1-.2 1.1.4 2.3.6 3.6.6.6 0 1 .4 1 1V20c0 .6-.4 1-1 1A17 17 0 0 1 3 4c0-.6.4-1 1-1h3.5c.6 0 1 .4 1 1 0 1.3.2 2.5.6 3.6.1.3 0 .7-.2 1z"/></svg>
        (325) 482-5096
      </li>
      <li>
        <svg viewBox="0 0 24 24" aria-hidden="true"><rect x="2" y="5" width="20" height="14" fill="var(--maroon)"/><path d="M3 6l9 7 9-7" stroke="var(--paper)" stroke-width="1.8" fill="none"/></svg>
        info@corvaneconstruction.com
      </li>
      <li>
        <svg viewBox="0 0 24 24" aria-hidden="true"><circle cx="12" cy="12" r="10" fill="var(--maroon)"/><path d="M2 12h20M12 2c3 3 3 17 0 20M12 2c-3 3-3 17 0 20" stroke="var(--paper)" stroke-width="1.6" fill="none"/></svg>
        corvaneconstruction.com
      </li>
    </ul>

    <address class="address">
      Corvane Construction<br>
      4875 FM 309<br>
      Harlow Bend, TX 79412
    </address>

    <svg class="base-band" viewBox="0 0 825 11" preserveAspectRatio="none" aria-hidden="true">
      <polygon points="0,0 536,0 530,11 0,11" fill="var(--maroon)"/>
      <polygon points="540,0 825,0 825,11 534,11" fill="var(--grey-band)"/>
    </svg>
  </section>

  <section class="card card-back" aria-label="Business card back">
    <div class="brand-back">
      <span class="brand-name">CORVANE</span>
      <span class="brand-sub">CONSTRUCTION</span>
    </div>

    <div class="services">
      <p>Roads • Substation Pads • Temporary Pads • Site Pads • Land Leveling</p>
      <p>Powerline Row Cleaning • Land Clearing • Gates • Fencing • Construction Entrances</p>
      <p>Excavation • Trenching • Underground Utilities • Directional Boring • Pile Driving</p>
    </div>
  </section>

</main>
</body>
</html>
```